Water ATM Card

Need a design for water ATM cards. Size of card is 3.375 x 2.125 inch
On the Front include the Cedar hollow Logo.
Bottom right corner should have Price $100
On the Back
This card is to be used to access water refills at any Cedar Hollow Water Vending Machines.
Please contact (869) 418 2930 or (869) 534 1276 or email clearflowbox@mailvista.example for any assistance or recharging of card.

```html
<!DOCTYPE html>
<html lang="en">
<head>
<meta charset="utf-8">
<title>Cedar Hollow Water Card</title>
<link href="https://fonts.googleapis.com/css2?family=Montserrat:wght@400;600;700&display=swap" rel="stylesheet">
<style>
  :root {
    --canvas: #ababab;
    --card-white: #ffffff;
    --deep-blue: #1a4799;
    --sky-blue: #2e93d1;
    --brand-blue: #1a6fb8;
    --text-white: #ffffff;
    --hill-green: #cfe6c4;
    --wave-blue: #c6d8ec;
  }
  * { box-sizing: border-box; margin: 0; padding: 0; }
  html, body { width: 1200px; height: 1000px; overflow: hidden; }
  body {
    background: var(--canvas);
    font-family: "Montserrat", sans-serif;
    position: relative;
  }
  .card {
    position: absolute;
    box-shadow: 0 18px 40px rgba(0,0,0,0.35);
    overflow: hidden;
  }
  .card--front {
    left: 294px; top: 78px; width: 615px; height: 352px;
    background: linear-gradient(90deg, var(--deep-blue) 15%, var(--sky-blue) 85%);
    color: var(--text-white);
  }
  .card--back {
    left: 294px; top: 483px; width: 613px; height: 352px;
    background: var(--card-white);
    color: var(--brand-blue);
  }
  .brand-name--front {
    position: absolute; left: 0; right: 0; top: 178px;
    text-align: center;
    font-weight: 700; font-size: 32px; line-height: 40px; letter-spacing: 0.5px;
  }
  .value-note {
    position: absolute; right: 280px; top: 299px;
    text-align: right; font-size: 12.5px; line-height: 16px; letter-spacing: 0.3px;
    text-transform: uppercase;
  }
  .value-amount {
    position: absolute; left: 346px; top: 293px;
    font-weight: 700; font-size: 40px; line-height: 1;
  }
  .back-art {
    position: absolute; left: 140px; top: 130px; width: 473px; height: 222px;
    background:
      linear-gradient(180deg, rgba(207,230,196,0) 0%, var(--hill-green) 55%, var(--wave-blue) 100%);
    -webkit-mask-image: linear-gradient(90deg, transparent 0%, #000 45%);
    mask-image: linear-gradient(90deg, transparent 0%, #000 45%);
  }
  .brand-name--back {
    position: absolute; left: 31px; top: 90px;
    font-weight: 700; font-size: 19px; line-height: 24px;
  }
  .card-usage {
    position: absolute; left: 31px; top: 142px; width: 240px;
    font-size: 14.5px; line-height: 19px;
  }
  .card-usage strong { font-weight: 700; }
  .contact-list {
    position: absolute; left: 33px; top: 244px; list-style: none;
    font-weight: 700; font-size: 14.5px; line-height: 19px;
  }
  .contact-list li { display: flex; align-items: center; gap: 9px; }
  .contact-list svg { width: 13px; height: 13px; fill: var(--brand-blue); }
</style>
</head>
<body>
  <section class="card card--front">
    <div class="brand-name brand-name--front">CEDAR HOLLOW</div>
    <p class="value-note">To be used to access<br>water refills</p>
    <div class="value-amount">$100</div>
  </section>

  <section class="card card--back">
    <div class="back-art" role="img" aria-label="Soft green hills and blue water backdrop"></div>
    <div class="brand-name brand-name--back">CEDAR HOLLOW</div>
    <p class="card-usage">This card is to be used to<br>access water refills at any<br><strong>Cedar Hollow Water<br>Vending Machines.</strong></p>
    <ul class="contact-list">
      <li><svg viewBox="0 0 24 24"><path d="M6.6 10.8c1.4 2.8 3.8 5.1 6.6 6.6l2.2-2.2c.3-.3.7-.4 1-.2 1.1.4 2.3.6 3.6.6.6 0 1 .4 1 1V20c0 .6-.4 1-1 1C10.6 21 3 13.4 3 4c0-.6.4-1 1-1h3.5c.6 0 1 .4 1 1 0 1.3.2 2.5.6 3.6.1.3 0 .7-.2 1z"/></svg>(869) 418 2930</li>
      <li><svg viewBox="0 0 24 24"><path d="M6.6 10.8c1.4 2.8 3.8 5.1 6.6 6.6l2.2-2.2c.3-.3.7-.4 1-.2 1.1.4 2.3.6 3.6.6.6 0 1 .4 1 1V20c0 .6-.4 1-1 1C10.6 21 3 13.4 3 4c0-.6.4-1 1-1h3.5c.6 0 1 .4 1 1 0 1.3.2 2.5.6 3.6.1.3 0 .7-.2 1z"/></svg>(869) 534 1276</li>
      <li><svg viewBox="0 0 24 24"><path d="M2 5h20v14H2z M3.5 6.5 12 12.5l8.5-6" fill="none" stroke="#1a6fb8" stroke-width="2.4"/></svg>clearflowbox@mailvista.example</li>
    </ul>
  </section>
</body>
</html>
```